Catalogue Design Project

We need a catalog design for a new private university called Redwell Institute Bayshore (see website www.rwi-bs.org). The catalog should be about 30 pages maximum and will include items such as General Information, Academic schedule, department descriptions, program descriptions, course descriptions, school policies, student services, admissions, San diego Lifestyle, etc.
I will provide the text but I need a professional design with regard to page layouts. I have provided some examples.
Ok, i posted the catalog content, just missing course descriptions.
Target Market(s)
Young Professionals, Foreign Students
Industry/Entity Type
University
Look and feel
Each slider illustrates characteristics of the customer's brand and the style your logo design should communicate.

```html
<!DOCTYPE html>
<html lang="en">
<head>
<meta charset="utf-8">
<title>Academic Programs – Language Acquisition</title>
<link href="https://fonts.googleapis.com/css2?family=Carlito:ital,wght@0,400;0,700;1,400&display=swap" rel="stylesheet">
<style>
  :root {
    --ink: #1a1a1a;
    --navy: #1f4f86;
    --navy-dark: #153a66;
    --steel: #2e5e93;
    --rule: #9fb6d1;
    --dot-grey: #a7a9ac;
    --footer-grey: #8a8a8a;
    --paper: #ffffff;
    --book-light: #efe4d0;
    --book-mid: #cdb790;
    --book-deep: #b39a6e;
  }
  * { margin: 0; padding: 0; box-sizing: border-box; }
  html, body { width: 927px; height: 1200px; overflow: hidden; background: var(--paper); }
  body { font-family: "Carlito", "Calibri", sans-serif; color: var(--ink); }
  .page { position: relative; width: 927px; height: 1200px; overflow: hidden; }

  .header-ornament {
    position: absolute; left: 58px; top: 58px; width: 154px; height: 34px;
    border-radius: 17px;
    background: linear-gradient(90deg, var(--navy) 0%, var(--dot-grey) 35%, var(--dot-grey) 70%, var(--navy) 100%);
  }
  .header-photo {
    position: absolute; right: 0; top: 0; width: 367px; height: 150px;
    background: linear-gradient(100deg, var(--paper) 0%, var(--book-light) 25%, var(--book-mid) 60%, var(--book-deep) 80%, var(--book-light) 100%);
  }
  .section-title {
    position: absolute; left: 303px; top: 94px; width: 318px; text-align: center;
    font-size: 29px; letter-spacing: .3px; color: #111;
  }
  .section-title-bar { position: absolute; left: 303px; top: 134px; width: 318px; height: 14px; background: var(--navy); }
  .header-rule { position: absolute; left: 0; top: 150px; width: 927px; height: 2px; background: var(--rule); }

  .tab {
    position: absolute; left: 42px; top: 178px; width: 385px; height: 43px;
    background: linear-gradient(180deg, var(--steel) 0%, var(--navy-dark) 100%);
    border-radius: 0 10px 10px 0; border: 2px solid #c8d6e8; border-left: none;
    color: #fff; font-size: 28px; line-height: 39px; padding-left: 16px; letter-spacing: .3px;
  }
  .tab-rule { position: absolute; left: 0; top: 198px; width: 42px; height: 2px; background: var(--rule); }

  .lead-title { position: absolute; left: 0; top: 244px; width: 927px; text-align: center; font-size: 23px; font-weight: 700; }
  .intro { position: absolute; left: 80px; width: 767px; font-size: 19.6px; line-height: 36.4px; }
  .intro--body { top: 282px; text-align: justify; }
  .intro--question { top: 500px; }
  .audience { position: absolute; left: 80px; top: 537px; width: 767px; list-style: none; font-size: 19.6px; line-height: 36.4px; }
  .audience li { position: relative; padding-left: 34px; }
  .audience li::before { content: "•"; position: absolute; left: 0; }

  .column { position: absolute; top: 704px; font-size: 19.6px; line-height: 27.3px; }
  .column--left { left: 80px; width: 385px; }
  .column--right { left: 503px; width: 342px; }
  .column h3 { font-weight: 400; text-decoration: underline; font-size: 19.6px; }
  .column p { text-align: justify; }
  .column .courses-label { margin-top: 27px; text-decoration: underline; }
  .course-list { list-style: none; font-size: 16.5px; line-height: 27.3px; margin-top: 2px; }

  .footer-rule { position: absolute; left: 0; top: 1156px; width: 927px; height: 1px; background: var(--rule); }
  .folio { position: absolute; right: 40px; top: 1170px; font-size: 13.5px; color: var(--footer-grey); letter-spacing: .3px; }
</style>
</head>
<body>
<div class="page">
  <div class="header-ornament" role="img" aria-label="Decorative cluster of blue and grey dots"></div>
  <div class="header-photo" role="img" aria-label="Photograph of an open book, fading into the page"></div>

  <div class="section-title">ACADEMIC PROGRAMS</div>
  <div class="section-title-bar"></div>
  <div class="header-rule"></div>

  <div class="tab-rule"></div>
  <div class="tab">LANGUAGE ACQUISITION</div>

  <h2 class="lead-title">English Language Fluency</h2>
  <p class="intro intro--body">Redwell Institute Bayshore has on staff well educated and experienced instructors who have lived in other countries and previously spent time learning a foreign language. In addition, our ESL faculty has at least a master's degree in a related field such as Linguistics, English, or TESOL. For these reasons, students at RWIB have the advantage of learning from teachers who are best adapted to getting them to fluency in a short time. Our teachers don't just teach, they do.</p>
  <p class="intro intro--question">What type of student is appropriate for our fluency program?</p>
  <ul class="audience">
    <li>Visitors who want to complement their travels with study</li>
    <li>Residents who need to improve their language skills for business</li>
    <li>Foreign Students needing to improve test scores for university admission</li>
    <li>Business leaders and executives who interact with English-speaking clients or associates</li>
  </ul>

  <section class="column column--left">
    <h3>Language Acquisition</h3>
    <p>Coursework focuses on helping students in all areas of communication: reading, writing, listening, and speaking while utilizing American history, culture, and activities for a well-rounded learning experience.</p>
    <div>Hours: 3 hours per week</div>
    <div>Length: 8 weeks per course</div>
    <div class="courses-label">Courses:</div>
    <ul class="course-list">
      <li>ENG 100 LEVEL I – FOUNDATIONS</li>
      <li>ENG 200 LEVEL II – GRAMMATICAL CONCEPTS</li>
      <li>ENG 300 LEVEL III – CONVERSATIONAL SKILLS</li>
      <li>ENG 400 LEVEL IV – SENTENCE STRUCTURE</li>
      <li>ENG 500 LEVEL V – ADVANCED FLUENCY</li>
    </ul>
  </section>

  <section class="column column--right">
    <h3>TEFA Preparation</h3>
    <p>Coursework for intermediate to advanced levels students wishing to prepare for passing the Test-Of-English-for-Academics college entrance exam. The course focuses on all sections of the actual examination.</p>
    <div>Hours: 3 hours per week</div>
    <div>Length: 4 weeks per course</div>
    <div class="courses-label">Courses:</div>
    <ul class="course-list">
      <li>ENG 105 – TEFA: Reading, Structure, and Writing</li>
      <li>ENG 205 – TEFA: Listening and Vocabulary</li>
      <li>ENG 305 – TEFA: Sample Tests</li>
    </ul>
  </section>

  <div class="footer-rule"></div>
  <div class="folio">6:: REDWELL INSTITUTE</div>
</div>
</body>
</html>
```